New Business Card Design Project

I need a design for business cards, i am an electrical business called "Corvane Electrical and Communications" i need the cards to be double sided with the company logo on the back (attached) the front needs to say my company name, web site, email address, telephone number, and ABN number and electrical license number. I am open to different arrangements of the information but would like the background to be incorporating something electrical or something that looks smart. open to all additional ideas also.

The company colours are orange and grey see logo attached.

Business Name: Corvane Electrical and Communications
Website: corvaneelectricalandcomms.example.com.au
Email: brent@corvaneelectricalandcomms.example.com.au
Telephone(mobile): 0481209736
ABN: 71208349162
Lic No: 418273D

Target Market(s)

Business entities, Project Managers, Accounts, Clients

Industry/Entity Type

Electrician

Contact Information for Business Card

I need a design for business cards, i am an electrical business called "Corvane Electrical and Communications" i need the cards to be double sided with the company logo on the back (attached) the front needs to say my company name

Font styles to use
Serif
Sans Serif

Colors
f37122
5c5c5c

Requirements
Must have
• Must have the Logo on the back open to different ways of it being on the back but had in mind to keep it central but again open to other options
Nice to have
• A real modern cool background that is eye catching yet contemporary
Should not have
• No backgrounds of a light bulb or plug or anything like that

```html
<!DOCTYPE html>
<html lang="en">
<head>
<meta charset="utf-8">
<title>Corvane Electrical and Communications – Business Card</title>
<link rel="stylesheet" href="https://fonts.googleapis.com/css2?family=Source+Sans+3:wght@400;600&display=swap">
<style>
  :root {
    --stage: #3b3b3b;
    --card-grey: #58585a;
    --brand-orange: #f9ac1b;
    --ink-white: #ffffff;
    --rule-grey: #9a9a9c;
  }
  * { margin: 0; padding: 0; box-sizing: border-box; }
  html, body {
    width: 1105px; height: 1200px; overflow: hidden;
    background: var(--stage);
    font-family: "Source Sans 3", "Helvetica Neue", Arial, sans-serif;
  }
  .canvas { position: relative; width: 1105px; height: 1200px; }

  .card {
    position: absolute; left: 196px; width: 720px; height: 412px;
    overflow: hidden;
  }

  /* Front */
  .card-front { top: 146px; background: var(--card-grey); color: var(--ink-white); }
  .brand-name {
    position: absolute; right: 36px; top: 70px;
    text-align: right; font-weight: 600; font-size: 26px; line-height: 1.15;
    letter-spacing: 1px; text-transform: uppercase; color: var(--ink-white);
  }
  .holder-name {
    position: absolute; left: 34px; top: 206px;
    font-size: 25px; font-weight: 600; color: var(--brand-orange); letter-spacing: .3px;
  }
  .holder-role {
    position: absolute; left: 34px; top: 238px;
    font-size: 19px; font-weight: 400; color: var(--ink-white);
  }
  .title-rule {
    position: absolute; left: 180px; right: 34px; top: 258px;
    height: 1px; background: var(--rule-grey);
  }
  .contact-list {
    position: absolute; left: 34px; top: 283px; list-style: none;
    font-size: 17.5px; line-height: 28px;
  }
  .contact-list li { display: flex; align-items: center; gap: 10px; }
  .contact-list svg { width: 16px; height: 16px; flex: none; }
  .registration {
    position: absolute; right: 34px; top: 311px; text-align: right;
    font-size: 18px; line-height: 28px;
  }
  .edge-rule {
    position: absolute; left: 0; right: 0; top: 386px; height: 4px; background: var(--ink-white);
  }
  .edge-band {
    position: absolute; left: 0; right: 0; top: 393px; bottom: 0; background: var(--brand-orange);
  }

  /* Back */
  .card-back { top: 602px; background: var(--brand-orange); color: var(--ink-white); }
  .back-brand {
    position: absolute; left: 0; right: 0; top: 178px; text-align: center;
    font-size: 52px; font-weight: 600; letter-spacing: 4px; text-transform: uppercase;
  }
  .back-web {
    position: absolute; left: 0; right: 0; top: 328px; text-align: center;
    font-size: 18px; letter-spacing: 1.5px;
  }
</style>
</head>
<body>
<main class="canvas">

  <section class="card card-front" aria-label="Business card front">
    <div class="brand-name">Corvane<br>Electrical &amp; Communications</div>

    <h1 class="holder-name">DANA WHITLOW</h1>
    <p class="holder-role">CEO/FOUNDER</p>
    <div class="title-rule"></div>

    <ul class="contact-list">
      <li>
        <svg viewBox="0 0 16 16" aria-hidden="true"><rect x="3.5" y="0.5" width="9" height="15" rx="1.5" fill="var(--brand-orange)"/><rect x="5" y="2.5" width="6" height="9" fill="var(--card-grey)"/></svg>
        <span>0481209736</span>
      </li>
      <li>
        <svg viewBox="0 0 16 16" aria-hidden="true"><rect x="0.5" y="3" width="15" height="10" fill="var(--brand-orange)"/><path d="M0.5 3 L8 9 L15.5 3" fill="none" stroke="var(--card-grey)" stroke-width="1.3"/></svg>
        <span>brent@corvaneelectricalandcomms.example.com.au</span>
      </li>
      <li>
        <svg viewBox="0 0 16 16" aria-hidden="true"><circle cx="8" cy="8" r="7.5" fill="var(--brand-orange)"/><path d="M4 5 Q7 4 7 7 Q5 8 6 11 M10 3 Q9 6 12 7 Q12 10 10 12" fill="none" stroke="var(--card-grey)" stroke-width="1.4"/></svg>
        <span>corvaneelectricalandcomms.example.com.au</span>
      </li>
    </ul>

    <div class="registration">
      <p>ABN: 71208349162</p>
      <p>Lic No: 418273D</p>
    </div>

    <div class="edge-rule"></div>
    <div class="edge-band"></div>
  </section>

  <section class="card card-back" aria-label="Business card back">
    <div class="back-brand">Corvane</div>
    <p class="back-web">www.corvaneelectricalandcomms.example.com.au</p>
  </section>

</main>
</body>
</html>
```